Brintel Works - Fast, Efficient and Gas Mainteance for Domestic, Commercial and Industrial clients

We are in the process of purchasing a new business and would like to get a new logo and business card.
Business is a gas maintenance business that also does new gas installations.
Has been established since 1988.
Services include:
Install all types of gas appliances & equipment inc. hot water units
Maintain / repair / replace all types of gas appliances & equipment

Target Market(s)

Domestic, Commercial and Industrial clients

Industry/Entity Type

Business

Contact Information for Business Card

admin@brintelworks.com.au
07 3918 4726
Brintel Works PTY LTD

Logo Text

Gas Fitting & Plumbing Maintenance Specialists

Font styles to use
Sans Serif

Requirements
Must have
• Logo
• Business name, contact number, email address, web address
• Domestic | Commercial | Industrial Est Since 1988
Nice to have
• Possibly a black card with a flame logo to one side
Should not have
• Spelling errors

```html
<!DOCTYPE html>
<html lang="en">
<head>
<meta charset="utf-8">
<title>Brintel Works — Business Card</title>
<link rel="stylesheet" href="https://fonts.googleapis.com/css2?family=Comfortaa:wght@400;700&display=swap">
<style>
  :root {
    --stage: #2a2a2a;
    --card: #1c1c1c;
    --card-edge: #0f0f0f;
    --text-grey: #a8a8a8;
    --text-light: #c9c9c9;
    --rule: #555555;
    --accent: #f2a521;
    --icon-ink: #1c1c1c;
  }
  * { box-sizing: border-box; margin: 0; padding: 0; }
  html, body {
    width: 1200px;
    height: 1189px;
    overflow: hidden;
    background: var(--stage);
    font-family: "Comfortaa", sans-serif;
  }
  .stage {
    position: relative;
    width: 1200px;
    height: 1189px;
  }
  .card {
    position: absolute;
    left: 190px;
    width: 820px;
    height: 470px;
    background: var(--card);
    border-radius: 34px;
    box-shadow: 0 18px 40px rgba(0,0,0,0.55), 0 0 0 1px var(--card-edge);
  }
  .card--front { top: 90px; }
  .card--back  { top: 630px; }

  /* Front: services */
  .front-brand {
    position: absolute;
    top: 90px;
    left: 0;
    right: 0;
    text-align: center;
  }
  .brand-mark {
    display: inline-flex;
    align-items: center;
    gap: 16px;
    color: var(--text-grey);
    font-size: 34px;
    font-weight: 400;
  }
  .brand-dot {
    width: 26px;
    height: 26px;
    border-radius: 50%;
    background: var(--accent);
    flex: none;
  }
  .since {
    display: flex;
    align-items: center;
    justify-content: center;
    gap: 14px;
    margin-top: 14px;
    color: var(--text-grey);
    font-size: 14px;
  }
  .since::before, .since::after {
    content: "";
    width: 150px;
    height: 1px;
    background: var(--rule);
  }
  .services-title {
    position: absolute;
    top: 232px;
    left: 0;
    right: 0;
    text-align: center;
    color: var(--text-grey);
    font-size: 26px;
    letter-spacing: 1px;
  }
  .services-list {
    position: absolute;
    top: 300px;
    left: 0;
    right: 0;
    text-align: center;
    list-style: none;
    color: var(--text-grey);
    font-size: 18px;
    line-height: 32px;
  }

  /* Back: contact */
  .back-brand {
    position: absolute;
    left: 0;
    top: 0;
    width: 405px;
    height: 100%;
    display: flex;
    align-items: center;
    justify-content: center;
  }
  .back-brand .brand-mark { font-size: 36px; }
  .divider {
    position: absolute;
    left: 405px;
    top: 60px;
    width: 1px;
    height: 300px;
    background: var(--rule);
  }
  .contact {
    position: absolute;
    left: 450px;
    top: 95px;
  }
  .person-name {
    color: var(--text-light);
    font-size: 32px;
  }
  .person-role {
    color: var(--accent);
    font-size: 20px;
    margin-top: 2px;
  }
  .contact-list {
    list-style: none;
    margin-top: 42px;
    color: var(--text-light);
    font-size: 22px;
  }
  .contact-list li {
    display: flex;
    align-items: center;
    gap: 8px;
    height: 32px;
  }
  .contact-icon {
    width: 22px;
    height: 22px;
    border-radius: 4px;
    background: var(--accent);
    display: flex;
    align-items: center;
    justify-content: center;
    flex: none;
  }
  .website {
    margin-top: 22px;
    color: var(--accent);
    font-size: 21px;
  }
</style>
</head>
<body>
<main class="stage">

  <section class="card card--front" aria-label="Card front: services">
    <div class="front-brand">
      <div class="brand-mark"><span class="brand-dot"></span>Brintel Works PTY LTD</div>
      <div class="since">since 1988</div>
    </div>
    <h2 class="services-title">SERVICES</h2>
    <ul class="services-list">
      <li>Install all types of gas appliances &amp; equipment inc. hot water units</li>
      <li>Maintain / repair / replace all types of gas appliances &amp; equipment</li>
    </ul>
  </section>

  <section class="card card--back" aria-label="Card back: contact details">
    <div class="back-brand">
      <div class="brand-mark"><span class="brand-dot"></span>Brintel Works</div>
    </div>
    <div class="divider"></div>
    <div class="contact">
      <p class="person-name">Employee Name</p>
      <p class="person-role">Owner</p>
      <ul class="contact-list">
        <li>
          <span class="contact-icon">
            <svg width="14" height="14" viewBox="0 0 24 24"><path fill="#1c1c1c" d="M6.6 10.8a15.1 15.1 0 0 0 6.6 6.6l2.2-2.2a1 1 0 0 1 1-.25 11.4 11.4 0 0 0 3.6.57 1 1 0 0 1 1 1V20a1 1 0 0 1-1 1A17 17 0 0 1 3 4a1 1 0 0 1 1-1h3.5a1 1 0 0 1 1 1 11.4 11.4 0 0 0 .57 3.6 1 1 0 0 1-.25 1z"/></svg>
          </span>07 3918 4726
        </li>
        <li>
          <span class="contact-icon">
            <svg width="14" height="14" viewBox="0 0 24 24"><path fill="#1c1c1c" d="M7 3h10v5H7zM4 9h16a2 2 0 0 1 2 2v6h-4v4H6v-4H2v-6a2 2 0 0 1 2-2zm4 7v3h8v-3z"/></svg>
          </span>07 3918 4730
        </li>
        <li>
          <span class="contact-icon">
            <svg width="14" height="14" viewBox="0 0 24 24"><path fill="none" stroke="#1c1c1c" stroke-width="2.4" d="M3 6h18v12H3zM3 6l9 7 9-7"/></svg>
          </span>admin@brintelworks.com.au
        </li>
      </ul>
      <p class="website">www.brintelworks.com.au</p>
    </div>
  </section>

</main>
</body>
</html>
```